Computer consultant business card

Bexil Software is a newly started computer consulting company. It's a small one-man company that provides mostly Vornix applications but also websites in collaboration with designers. I'm running this company on the side of full time university studies.

I want the final design to be clean and memorable. Be creative! :)

Some inspiration:
http://www.pixelmarta.com/design/48317
http://www.pixelmarta.com/design/2739164/business-card-design-by-frostlynk
http://www.pixelmarta.com/design/604281/business-card-design-by-koralind-vestrabanu

See attachment for my company logo.
Updates

I would like to thank everyone for submitting! I'll need a couple of days to review and ultimately select a design.

Target Market(s)

Non-technical entrepreneurs and small companies.

Industry/Entity Type

University

Requirements
Must have
• My company logo.
In any way, both colors from my logo.
First- and last name, e-mail and phone number.
Double-sided design.
Nice to have
• Something creative with the symbol in my logo

```html
<!DOCTYPE html>
<html lang="en">
<head>
<meta charset="utf-8">
<title>Bexil Software — Business Card</title>
<link rel="stylesheet" href="https://fonts.googleapis.com/css2?family=Montserrat:wght@400;500;600;700&display=swap">
<style>
  :root {
    --page-bg: #e6e6e6;
    --brand-blue: #3d66a8;
    --brand-blue-deep: #335995;
    --brand-blue-light: #4a76b8;
    --ink: #2b2b2d;
    --paper: #ffffff;
    --soft-grey: #dcdcdc;
    --soft-lilac: #e6e9f4;
  }
  * { box-sizing: border-box; margin: 0; padding: 0; }
  html, body { width: 1200px; height: 1016px; overflow: hidden; }
  body {
    background: var(--page-bg);
    font-family: "Montserrat", sans-serif;
    position: relative;
  }
  .card {
    position: absolute;
    left: 260px;
    width: 680px;
    height: 390px;
    border-radius: 30px;
    overflow: hidden;
    box-shadow: 0 10px 28px rgba(0,0,0,0.18);
  }
  .card--front { top: 90px; background: var(--brand-blue-deep); }
  .card--back { top: 536px; background: var(--paper); }
  .card__art { position: absolute; inset: 0; width: 100%; height: 100%; }

  .wordmark {
    position: absolute;
    display: flex;
    align-items: center;
    gap: 18px;
    font-weight: 600;
    letter-spacing: 1px;
  }
  .wordmark__dot { border-radius: 50%; flex: none; }
  .card--front .wordmark {
    left: 50%; top: 50%;
    transform: translate(-50%, -50%);
    color: var(--paper);
    font-size: 82px;
  }
  .card--front .wordmark__dot { width: 70px; height: 70px; background: var(--paper); }
  .card--back .wordmark {
    left: 40px; top: 96px;
    color: var(--ink);
    font-size: 60px;
  }
  .card--back .wordmark__dot { width: 52px; height: 52px; background: var(--brand-blue); }

  .holder {
    position: absolute;
    right: 46px; top: 48px;
    text-align: right;
    color: var(--paper);
  }
  .holder__name { font-size: 26px; font-weight: 600; letter-spacing: 1px; }
  .holder__title { font-size: 17px; font-weight: 700; margin-top: 2px; }

  .contact {
    position: absolute;
    right: 46px; bottom: 70px;
    list-style: none;
    color: var(--paper);
    text-align: right;
    font-size: 18px;
    font-weight: 400;
    letter-spacing: 0.5px;
    line-height: 1.7;
  }
  .contact li { display: flex; align-items: center; justify-content: flex-end; gap: 10px; white-space: nowrap; }
  .contact svg { width: 16px; height: 16px; flex: none; }
</style>
</head>
<body>

  <section class="card card--front" aria-label="Card front">
    <svg class="card__art" viewBox="0 0 680 390" aria-hidden="true">
      <defs>
        <radialGradient id="frontGlow" cx="50%" cy="48%" r="45%">
          <stop offset="0%" stop-color="#4a76b8"/>
          <stop offset="100%" stop-color="#3d66a8"/>
        </radialGradient>
      </defs>
      <rect width="680" height="390" fill="#335995"/>
      <circle cx="360" cy="190" r="170" fill="url(#frontGlow)"/>
    </svg>
    <div class="wordmark"><span class="wordmark__dot"></span><span class="wordmark__name">bexil</span></div>
  </section>

  <section class="card card--back" aria-label="Card back">
    <svg class="card__art" viewBox="0 0 680 390" aria-hidden="true">
      <defs>
        <radialGradient id="backGlow" cx="65%" cy="45%" r="55%">
          <stop offset="0%" stop-color="#4a76b8"/>
          <stop offset="100%" stop-color="#3d66a8"/>
        </radialGradient>
      </defs>
      <circle cx="190" cy="335" r="115" fill="#e6e9f4"/>
      <circle cx="172" cy="325" r="88" fill="#dcdcdc"/>
      <path d="M300,0 C380,60 380,220 320,390 L680,390 L680,0 Z" fill="url(#backGlow)"/>
      <path d="M278,0 C358,60 358,220 298,390" fill="none" stroke="#2b2b2d" stroke-width="12"/>
    </svg>
    <div class="wordmark"><span class="wordmark__dot"></span><span class="wordmark__name">bexil</span></div>
    <div class="holder">
      <p class="holder__name">YOUR NAME</p>
      <p class="holder__title">Job Title</p>
    </div>
    <ul class="contact">
      <li>000-000-000
        <svg viewBox="0 0 16 16" aria-label="Phone"><rect x="4" y="1" width="8" height="14" rx="1.5" fill="none" stroke="#fff" stroke-width="1.4"/></svg>
      </li>
      <li>name@domainname.com
        <svg viewBox="0 0 16 16" aria-label="Email"><rect x="1" y="3" width="14" height="10" fill="#fff"/><path d="M1,3 L8,9 L15,3" fill="none" stroke="#3d66a8" stroke-width="1.3"/></svg>
      </li>
    </ul>
  </section>

</body>
</html>
```